Wordpress Theme for Northgate Clinic

** Please view updated Sitemap2.pdf doc to clarify some confusion ***

This is a multiuser WordPress subscription site for NORTHGATE CLINIC. Please see attachment for sitemap. Please do not include extra content like social media icons, search bars, or images. If you have questions, please ask for clarification.
The site contains the following pages and sub-pages:

1. Home
2. Our Clinic
2a. Our Clinic > Mission
2b. Our Clinic > Services
2c. Our Clinic > Clinic Policies
2d. Our Clinic > Schedules
3. Our Staff
3a. Our Staff > [Staff member page]
4. Resources
4a. Resources > Patient Health (index)
4b. Resources > Patient Health (index) > [post]
4c. Resources > Links
4d. Resources > Forms
5. Alerts
5a. Alerts > [Alert Page]
6. Contact Us

Includes the Following Pages, Subpages, and Content
1. Home
a. About Us
b. Our Staff
c. Bulletins
d. Accepting New Patients (shown as an alert widget)
e. Links
i. Physician Toolbox
ii. Book an Appointment
f. Clinic Policies
i. Show first 3 policies (e.g. Late Arrivals, Missed Appointments, Fees)
ii. Link to Clinic Policies page
g. Primary widget (displayed on all pages)
i. Hours of operation
ii. Contact Info
1. Tel
2. Fax
3. Email
4. Address
5. Get directions (link to Google Maps)
2. Our Clinic
a. Main Page
i. Clinic Name
ii. Overview
iii. Languages Spoken
iv. Secondary Navigation
1. Mission
2. Services
3. Clinic Policies
4. Schedules (see attachment)
b. Our Clinic > Mission
c. Our Clinic > Services
i. For each service include service TITLE and DESCRIPTION
d. Our Clinic > Clinic Policies
i. For each policy include policy TITLE and DESCRIPTION
ii. Include the following policies in mockup
1. Late arrivals
2. Missed appointments
3. Fees for missed appointments
4. Referrals and follow-ups
5. Services not covered by RDA
6. Information for LTF patients
7. Medical Legal Reports
e. Our Clinic > Schedules
3. Our Staff
a. Main Page
i. Display a list of staff members. Include NAME and DESIGNATION
b. Our Staff > [Staff Name]
i. Include NAME, PICTURE, DESIGNATION, and BIO
4. Resources
a. Resources > Patient Health
i. Main Page
1. Posts (ordered by date)
a. Title
b. Summary
2. Side Navigation
a. Post Categories
ii. Patient Health > [post title]
1. Title
2. Post Category
3. Date
4. Author
5. Summary
6. Body
b. Resources > Links
1. Secondary Navigation - Categories
a. Sample Categories:
i. Local Services
ii. RDA and Drug Coverage
iii. Mental Health Resources
2. Category page
a. Include the following links in the 'Local Services' category
i. Hypertension clinics
ii. Home Care services
iii. Vaccine Clinics
c. Resources > Forms
i. Display a table with form TITLE and CATEGORY
ii. Side Navigation
1. Form Categories
a. Use the following sample Categories
i. Referrals
ii. Insurance
iii. Intake
iv. Discharge
v. Waivers
5. Alerts
a. Main page
i. List of all Alert posts
1. Include post TITLE as a link to the post
ii. Side Navigation
1. Alerts Archive
a. shown as Month + Number of posts
iii. Alerts > [Alert page]
1. Include TITLE, DATE, AUTHOR, BODY
6. Contact Us
a. Map
b. Hours of operation
c. Address
d. Phone number
e. Fax number
e. Fax number
f. Map
g. Email

Design notes:
- fixed width
- responsive (need designs for mobile, tablet, and desktop)
- simple, dark font, white background
- use Font Awesome icons where needed
- user adds own logo

Target Market(s)

Northgate Clinic

Industry/Entity Type

Medical

Number of Pages Required

5+ page

Font styles to use
Serif
Sans Serif

Requirements
Must have
• Please keep designs very simple.
• Examples:
• https://www.quolbin.com/install
• http://www.ventrohax.com/company/about-us
• http://brindlequota.org/
• http://www.trosk.com/
Should not have
• Minimal or no use of shadows and gradients

```html
<!DOCTYPE html>
<html lang="en">
<head>
<meta charset="utf-8">
<title>Northgate Clinic – Contact Us</title>
<link href="https://fonts.googleapis.com/css2?family=Open+Sans:wght@400;600;700&display=swap" rel="stylesheet">
<style>
:root{
  --brand:#0a86d8;
  --ink:#222;
  --text:#333;
  --muted:#888;
  --band:#f7f7f7;
  --line:#d9d9d9;
  --footer:#2b2b2b;
  --footer-head:#9a9a9a;
  --footer-link:#888;
  --white:#fff;
}
*{box-sizing:border-box;margin:0;padding:0}
html,body{width:1200px;height:720px;overflow:hidden}
body{font-family:"Open Sans",Arial,sans-serif;color:var(--text);background:var(--white);position:relative}
a{color:inherit;text-decoration:none}
.abs{position:absolute}

.topbar{left:0;top:0;width:1200px;height:30px;background:var(--brand);color:var(--white);font-size:9.5px}
.topbar .help{left:161px;top:9px}
.topbar .help span+span{border-left:1px solid var(--white);margin-left:4px;padding-left:4px}
.topbar .quick{right:161px;top:9px}
.topbar .quick a+a{border-left:1px solid var(--white);margin-left:6px;padding-left:6px}

.header{left:0;top:30px;width:1200px;height:83px}
.brand{left:161px;top:26px;display:flex;align-items:center;gap:12px}
.brand-dot{width:22px;height:22px;border-radius:50%;background:var(--brand)}
.brand-name{font-size:20px;font-weight:600;color:var(--ink)}
.main-nav{top:0;height:83px;font-size:11px;color:var(--text)}
.main-nav a{position:absolute;top:33px;white-space:nowrap}
.main-nav .current{top:0;left:978px;width:60px;height:83px;background:var(--brand);color:var(--white);text-align:center;padding-top:33px}

.page-band{left:0;top:113px;width:1200px;height:59px;background:var(--band)}
.page-title{left:161px;top:14px;font-size:11px;font-weight:700;color:var(--ink)}
.crumbs{left:162px;top:33px;font-size:10px;color:var(--ink)}

.map{left:161px;top:210px;width:277px;height:202px;background:linear-gradient(135deg,#e9e5dc,#dcd8cf 60%,#e4e0d6)}

.about{left:460px;top:214px;width:280px}
.about h2{font-size:12px;font-weight:700;color:var(--ink);margin-bottom:13px}
.about p{font-size:8.5px;line-height:13.5px;margin-bottom:14px;padding-left:1px;width:272px}
.about h3{font-size:10px;font-weight:700;color:var(--ink);margin-bottom:6px}
.info{display:grid;grid-template-columns:94px 1fr;font-size:9.5px;line-height:15px;padding-left:1px}

.hours{left:762px;top:210px;width:277px;height:195px;border:1px solid var(--line)}
.hours h3{background:var(--brand);color:var(--white);font-size:10px;font-weight:700;height:33px;padding:10px 13px}
.hours dl{display:grid;grid-template-columns:1fr auto;padding:19px 14px 0 13px;font-size:9.5px;line-height:15px}
.hours dd{text-align:right}

.footer{left:0;top:493px;width:1200px;height:192px;background:var(--footer);border-top:4px solid var(--brand)}
.footer .brand{top:39px}
.footer .brand-name{color:var(--white)}
.footer-about{left:162px;top:85px;width:200px;font-size:8.5px;line-height:13.5px;color:#ddd}
.fcol{top:32px}
.fcol h4{font-size:12px;font-weight:700;color:var(--footer-head);margin-bottom:5px}
.fcol ul{list-style:none;font-size:9.5px;line-height:18px;color:var(--footer-link)}
.fcol .active{color:#ccc}
.fcontact{display:grid;grid-template-columns:89px 1fr;font-size:9.5px;line-height:15px;color:var(--footer-link);padding-left:2px;margin-top:8px}

.legal{left:0;top:685px;width:1200px;height:35px;background:var(--footer);border-top:1px solid #555;font-size:9.5px;color:var(--footer-link)}
.legal span{position:absolute;top:9px}
</style>
</head>
<body>
<div class="abs topbar">
  <div class="abs help"><span>To help Here : 210 480 7716</span><span>Email : hello@northgateclinic.ca</span></div>
  <div class="abs quick"><a href="#">Book an Appointment</a><a href="#">Physician Toolbox</a></div>
</div>

<header class="abs header">
  <a class="abs brand" href="#"><span class="brand-dot"></span><span class="brand-name">Northgate Clinic</span></a>
  <nav class="abs main-nav">
    <a href="#" style="left:566px">Home</a>
    <a href="#" style="left:634px">Our Clinic</a>
    <a href="#" style="left:721px">Newsletter</a>
    <a href="#" style="left:813px">Our Staff</a>
    <a href="#" style="left:896px">Resources</a>
    <a href="#" class="current">Contact Us</a>
  </nav>
</header>

<div class="abs page-band">
  <h1 class="abs page-title">CONTACT US</h1>
  <div class="abs crumbs">HOME / CONTACTUS</div>
</div>

<div class="abs map" role="img" aria-label="Street map showing the clinic location downtown"></div>

<section class="abs about">
  <h2>NORTHGATE CLINIC</h2>
  <p>Lorem Ipsum is simply dummy text of the printing and ypesetting industry. Lorem Ipsum has been the industry's standard dummy text ever since</p>
  <h3>CONTACT INFO</h3>
  <div class="info">
    <span>Telephone :</span><span>250-318-4420</span>
    <span>Fax:</span><span>250-318-4421</span>
    <span></span><span>250-318-4422</span>
    <span>Email:</span><span>hello@northgateclinic.ca</span>
    <span>Address:</span><span>48 Alder Row Kelbrook,B.<br>Canada, K2P 4LM</span>
  </div>
</section>

<section class="abs hours">
  <h3>HOURS OF OPRATION</h3>
  <dl>
    <dt>Monday :</dt><dd>8:00 AM - 6:00 PM</dd>
    <dt>Tuesday :</dt><dd>8:00 AM - 6:00 PM</dd>
    <dt>Wednesday :</dt><dd>8:00 AM - 6:00 PM</dd>
    <dt>Thursday :</dt><dd>8:00 AM - 6:00 PM</dd>
    <dt>Friday :</dt><dd>8:00 AM - 6:00 PM</dd>
    <dt>Saturday :</dt><dd>9:00 AM - 4:00 PM</dd>
    <dt>Sunday :</dt><dd>9:00 AM - 4:00 PM</dd>
  </dl>
</section>

<footer class="abs footer">
  <a class="abs brand" href="#"><span class="brand-dot"></span><span class="brand-name">Northgate Clinic</span></a>
  <p class="abs footer-about">Lorem Ipsum is simply dummy text of the printing and typesetting industry. Lorem Ipsum has been the industry's standard dummy text</p>
  <div class="abs fcol" style="left:461px">
    <h4>Navigation</h4>
    <ul><li class="active">Home</li><li>Our Clinic</li><li>Newsletter</li><li>Our Staff</li><li>Resources</li></ul>
  </div>
  <div class="abs fcol" style="left:686px">
    <h4>Links</h4>
    <ul><li>Help</li><li>Support</li><li>Privacy Policy</li></ul>
  </div>
  <div class="abs fcol" style="left:836px;top:30px">
    <h4>Contact Us</h4>
    <div class="fcontact">
      <span>Telephone :</span><span>250-318-4420</span>
      <span>Email:</span><span>hello@northgateclinic.ca</span>
      <span>Address:</span><span>48 Alder Row<br>Kelbrook,B. Canada,<br>K2P 4LM</span>
    </div>
  </div>
</footer>

<div class="abs legal">
  <span style="left:162px">© 2015 Northgate Clinic. All Rights Reservsd</span>
  <span style="left:463px">About Us</span>
  <span style="left:530px">Terms of Use</span>
  <span style="left:615px">Privacy Policy</span>
</div>
</body>
</html>
```